Jolly Paws Business Card Update

I have a business card which I love. I want to keep the same logo, colours, font and style. I want to upgrade the scripting and remove some elements and add others.
On the front side under Services - remove the existing wording and insert - Providing individual coaching strategies to create happy, healthy and social canine companions
Under Denise Carvell amend the current wording to read: Qualified in Dog Behavioural Training, Natural Animal Healthcare and Animal Health Science
On the reverse side to remove the web address.

```html
<!DOCTYPE html>
<html lang="en">
<head>
<meta charset="utf-8">
<title>Jolly Paws Business Card</title>
<link rel="stylesheet" href="https://fonts.googleapis.com/css2?family=Arimo:wght@400;700&family=Open+Sans:ital,wght@0,400;0,600;1,400&display=swap">
<style>
  :root {
    --backdrop: #2b2b2b;
    --blue-light: #0790cf;
    --blue-mid: #1c5cab;
    --blue-deep: #283f8e;
    --red-dark: #7c1a1e;
    --red: #c8181f;
    --cream: #efe8d4;
    --cream-dark: #c9bf9f;
    --white: #ffffff;
    --text-soft: #e6ecf7;
  }
  * { box-sizing: border-box; margin: 0; padding: 0; }
  html, body { width: 1200px; height: 1138px; overflow: hidden; }
  body { background: var(--backdrop); font-family: "Arimo", Arial, sans-serif; color: var(--white); position: relative; }

  .card {
    position: absolute;
    border-radius: 14px;
    overflow: hidden;
    background: linear-gradient(205deg, var(--blue-light) 0%, var(--blue-mid) 50%, var(--blue-deep) 100%);
    box-shadow: 0 6px 12px rgba(0,0,0,.55);
  }
  .card--front { left: 274px; top: 186px; width: 623px; height: 376px; }
  .card--back { left: 276px; top: 608px; width: 618px; height: 374px; }

  .brand-name { position: absolute; font-family: "Arimo", Arial, sans-serif; font-weight: 400; color: var(--white); letter-spacing: 1.5px; white-space: nowrap; }
  .brand-tagline { position: absolute; font-size: 17px; color: var(--white); letter-spacing: .2px; white-space: nowrap; }

  .card--front .brand-name { left: 34px; top: 52px; font-size: 36px; }
  .card--front .brand-tagline { left: 34px; top: 91px; }

  .services { position: absolute; left: 38px; top: 183px; width: 240px; font-size: 16px; line-height: 19px; color: var(--text-soft); }
  .services h2 { font-size: 16px; font-weight: 700; line-height: 19px; }

  .badge { position: absolute; border-radius: 50%; background: radial-gradient(circle, var(--cream) 55%, var(--cream-dark) 100%); border: solid var(--red); box-shadow: inset 0 0 0 2px var(--red-dark); }
  .card--front .badge { left: 328px; top: 38px; width: 260px; height: 260px; border-width: 24px; }
  .card--back .badge { left: 32px; top: 38px; width: 116px; height: 116px; border-width: 11px; }

  .front-band { position: absolute; left: 0; bottom: 0; width: 100%; height: 52px; background: linear-gradient(90deg, var(--red-dark), var(--red) 55%, var(--red-dark)); padding-left: 33px; display: flex; align-items: center; font-size: 17px; }

  .card--back .brand-name { left: 170px; top: 58px; font-size: 44px; }
  .card--back .brand-tagline { left: 170px; top: 110px; font-size: 19px; }

  .person { position: absolute; left: 30px; top: 200px; }
  .person-name { font-family: "Open Sans", Arial, sans-serif; font-weight: 600; font-size: 25px; line-height: 30px; }
  .person-quals { font-family: "Open Sans", Arial, sans-serif; font-style: italic; font-size: 15.5px; line-height: 21px; color: var(--text-soft); margin-top: 4px; }

  .contacts { position: absolute; left: 343px; top: 208px; list-style: none; font-family: "Open Sans", Arial, sans-serif; font-size: 16.5px; }
  .contacts li { display: flex; align-items: center; height: 23px; }
  .contacts svg { width: 14px; height: 14px; margin-right: 14px; fill: var(--white); }

  .back-footer-left { position: absolute; left: 30px; top: 325px; font-size: 17px; }
  .back-footer-strip { position: absolute; left: 0; bottom: 0; width: 100%; height: 46px; }
  .back-footer-right { position: absolute; left: 282px; top: 340px; font-size: 17px; white-space: nowrap; }
</style>
</head>
<body>
  <section class="card card--front">
    <div class="brand-name">JOLLY PAWS</div>
    <div class="brand-tagline">HAPPY DOGS, HAPPY OWNERS</div>
    <div class="services">
      <h2>SERVICES</h2>
      <p>Providing individual coaching strategies to create happy, healthy and social canine companions</p>
    </div>
    <div class="badge"></div>
    <div class="front-band">Promoting communication and connection between dogs and their families</div>
  </section>

  <section class="card card--back">
    <div class="badge"></div>
    <div class="brand-name">JOLLY PAWS</div>
    <div class="brand-tagline">HAPPY DOGS, HAPPY OWNERS</div>
    <div class="person">
      <div class="person-name">Denise Carvell</div>
      <p class="person-quals">Qualified in Dog Behavioural Training,<br>Natural Animal Healthcare and<br>Animal Health Science</p>
    </div>
    <ul class="contacts">
      <li><svg viewBox="0 0 14 14"><rect x="3" y="0" width="8" height="14" rx="1.5"/><rect x="4.5" y="2" width="5" height="4" fill="#1c5cab"/></svg>0400 628175</li>
      <li><svg viewBox="0 0 14 14"><rect x="0" y="3" width="14" height="9"/><path d="M0 3 L7 8 L14 3" stroke="#1c5cab" stroke-width="1.2" fill="none"/></svg>jollypaws1@pawmail.com</li>
    </ul>
    <div class="back-footer-left">Promoting Communication</div>
    <svg class="back-footer-strip" viewBox="0 0 618 46" preserveAspectRatio="none">
      <defs>
        <linearGradient id="strip-cream" x1="0" y1="0" x2="0" y2="1"><stop offset="0" stop-color="#f3ecd8"/><stop offset="1" stop-color="#bfb493"/></linearGradient>
        <linearGradient id="strip-red" x1="0" y1="0" x2="1" y2="0"><stop offset="0" stop-color="#8a1a1f"/><stop offset=".6" stop-color="#c8181f"/><stop offset="1" stop-color="#b8161c"/></linearGradient>
      </defs>
      <rect x="0" y="32" width="262" height="14" fill="url(#strip-cream)"/>
      <polygon points="270,0 618,0 618,46 256,46" fill="url(#strip-red)"/>
    </svg>
    <div class="back-footer-right">Connection between dogs &amp; their families</div>
  </section>
</body>
</html>
```